Executive Performance Review mapped on J-curve

I need to turn an executive company performance review into a visual infographic. The list of accomplishments is grouped into four calendar quarters. Each quarter needs a subtle representation of the season. The four quarters and associated list of accomplishments need to be mapped to a J-curve. - Spreadsheet with accomplishments attached (Marlowbend)- Sample image of a J-curve. You can google J-curve to see more images.- The title should be "Danica Ostrander Year in Review"

Target Market(s)

Board of Directors

Requirements
Nice to have
• This will be presented to a company founder that is an artist and customer experience expert. He is very visual so a nice visual representation of the data will be impactful. He also uses the phrase that you have to live with or work with someone for four seasons before you really know them. This is why I have the seasons mapped to the quarters. The Fall season motif should be gloomy and stormy.

```html
<!DOCTYPE html>
<html lang="en">
<head>
<meta charset="utf-8">
<title>Danica Ostrander – Year One in Review</title>
<link href="https://fonts.googleapis.com/css2?family=Libre+Franklin:wght@700;800&family=Source+Sans+3:wght@400;600;700&display=swap" rel="stylesheet">
<style>
:root{
  --ink:#1e1e1e;
  --title:#3a3a3a;
  --sum-band:#f9c80e;--sum-tab:#fbe98a;--sum-bg:#fffbe6;
  --fal-band:#4a5a66;--fal-tab:#8fa0a8;--fal-bg:#dde9ea;
  --win-band:#a9d8e3;--win-tab:#d3eef3;--win-bg:#eef8fa;
  --spr-band:#c6e05a;--spr-tab:#e3f0a8;--spr-bg:#f4f8e3;
  --grn-band:#2e8b3a;--grn-tab:#5aa84a;--grn-bg:#dce9dc;
}
*{margin:0;padding:0;box-sizing:border-box}
html,body{width:1200px;height:719px;overflow:hidden;background:#fff}
body{position:relative;font-family:"Source Sans 3",Arial,sans-serif;color:var(--ink)}
.heading{position:absolute;left:60px;top:42px;color:var(--title)}
.heading h1{font-family:"Libre Franklin",Arial,sans-serif;font-weight:800;font-size:22px;letter-spacing:-.2px;line-height:1}
.heading .date{font-size:19px;line-height:1.1;margin-top:2px}
.heading .company{font-size:15px;line-height:1.1;color:#555}
.board{position:absolute;left:0;top:0}
.season{position:absolute;top:113px;width:217px;height:557px}
.season .band{height:18px;text-align:center;color:#fff;font-weight:700;font-size:12px;line-height:18px;letter-spacing:.3px}
.season .tab{width:106px;margin:0 auto;height:17px;border-radius:0 0 8px 8px;text-align:center;font-weight:700;font-size:9.5px;line-height:17px}
.summer{left:58px}.summer .band{background:var(--sum-band)}.summer .tab{background:var(--sum-tab)}
.fall{left:275px}.fall .band{background:var(--fal-band)}.fall .tab{background:var(--fal-tab);color:#1e2a30}
.winter{left:492px}.winter .band{background:var(--win-band)}.winter .tab{background:var(--win-tab)}
.spring{left:709px}.spring .band{background:var(--spr-band)}.spring .tab{background:var(--spr-tab)}
.greenfield{left:926px}.greenfield .band{background:var(--grn-band)}.greenfield .tab{background:var(--grn-tab);color:#fff}
.notes{position:absolute;left:24px;top:44px;right:4px;font-size:9px;line-height:13.6px}
.greenfield .notes{right:60px}
.block{position:relative;margin-bottom:10px}
.block h3{font-size:9.4px;font-weight:700;line-height:13px}
.block li{list-style:none}
.block li::before{content:"• "}
.block .plain::before{content:""}
.icon{position:absolute;left:-20px;top:3px;width:15px;height:15px}
.label{position:absolute;top:655px;width:217px;text-align:center;font-weight:700;font-size:9.5px;letter-spacing:.2px}
.value{position:absolute;width:40px;height:40px;border-radius:50%;color:#fff;font-weight:700;font-size:8px;line-height:10px;text-align:center;display:flex;align-items:center;justify-content:center}
</style>
</head>
<body>
<svg class="board" width="1200" height="719" viewBox="0 0 1200 719" role="img" aria-label="Seasonal scenes beneath the J-curve: sunny beach, stormy autumn rain, snowy winter field, spring meadow, green growth">
  <defs>
    <clipPath id="below-curve"><path d="M58,520 C130,548 250,590 383,592 C480,593 560,565 708,505 C800,465 880,410 925,365 C990,305 1080,215 1141,130 L1141,670 L58,670 Z"/></clipPath>
    <linearGradient id="sun" x1="0" y1="0" x2="0" y2="1"><stop offset="0" stop-color="#fde37a"/><stop offset="1" stop-color="#f6c21a"/></linearGradient>
    <linearGradient id="storm" x1="0" y1="0" x2="0" y2="1"><stop offset="0" stop-color="#5d666d"/><stop offset="1" stop-color="#8f979c"/></linearGradient>
    <linearGradient id="snow" x1="0" y1="0" x2="0" y2="1"><stop offset="0" stop-color="#bfe6f2"/><stop offset="1" stop-color="#eefafd"/></linearGradient>
    <linearGradient id="meadow" x1="0" y1="0" x2="0" y2="1"><stop offset="0" stop-color="#e4f2b0"/><stop offset="1" stop-color="#b8da52"/></linearGradient>
    <linearGradient id="growth" x1="0" y1="0" x2="1" y2="0"><stop offset="0" stop-color="#a7d25a"/><stop offset="1" stop-color="#2e8b3a"/></linearGradient>
  </defs>
  <rect x="58" y="113" width="217" height="557" fill="var(--sum-bg)"/>
  <rect x="275" y="113" width="217" height="557" fill="var(--fal-bg)"/>
  <rect x="492" y="113" width="217" height="557" fill="var(--win-bg)"/>
  <rect x="709" y="113" width="217" height="557" fill="var(--spr-bg)"/>
  <rect x="926" y="113" width="216" height="557" fill="var(--grn-bg)"/>
  <g clip-path="url(#below-curve)">
    <rect x="58" y="110" width="217" height="560" fill="url(#sun)"/>
    <rect x="275" y="110" width="217" height="560" fill="url(#storm)"/>
    <rect x="492" y="110" width="217" height="560" fill="url(#snow)"/>
    <rect x="709" y="110" width="217" height="560" fill="url(#meadow)"/>
    <rect x="926" y="110" width="216" height="560" fill="url(#growth)"/>
  </g>
  <path d="M58,520 C130,548 250,590 383,592 C480,593 560,565 708,505 C800,465 880,410 925,365 C990,305 1080,215 1141,130" fill="none" stroke="#3c4a52" stroke-width="4" stroke-opacity=".55"/>
  <g stroke="#9aa" stroke-dasharray="2 2" stroke-width="1"><line x1="275" y1="131" x2="275" y2="670"/><line x1="492" y1="131" x2="492" y2="670"/><line x1="709" y1="131" x2="709" y2="670"/></g>
</svg>

<header class="heading">
  <h1>DANICA OSTRANDER - YEAR ONE IN REVIEW</h1>
  <p class="date">JULY 1, 2019</p>
  <p class="company">KESTREL FORGE, INC.</p>
</header>

<section class="season summer">
  <div class="band">SUMMER</div><div class="tab">Q3 2018</div>
  <div class="notes">
    <div class="block"><svg class="icon" viewBox="0 0 15 15"><rect x="1" y="3" width="10" height="10" fill="none" stroke="#333"/><path d="M7 8 14 1M10 1h4v4" fill="none" stroke="#333"/></svg>
      <h3>TRANSITIONS</h3><ul><li>RO Transition from Reid &amp; Lina</li><li>Start CR Office Initiative</li><li>Tactical Ops transition from Reid</li><li>Formalize Exec Team</li></ul></div>
    <div class="block"><svg class="icon" viewBox="0 0 15 15"><circle cx="3" cy="7.5" r="2" fill="none" stroke="#333"/><rect x="10" y="1" width="4" height="4" fill="none" stroke="#333"/><rect x="10" y="10" width="4" height="4" fill="none" stroke="#333"/><path d="M5 7.5h3V3h2M8 7.5V12h2" fill="none" stroke="#333"/></svg>
      <h3>BIZ ARCHITECTURE</h3><ul><li>Independent Financial Audit</li><li>Organizational Audit - Structure</li><li>Organizational Audit - People</li><li>XF Framework - ESU</li><li>Defined Utilization, Realization, Availability</li></ul></div>
    <div class="block"><svg class="icon" viewBox="0 0 15 15"><path d="M1 3l3 3M4 3 1 6M1 10h3M10 12l3-3" fill="none" stroke="#333"/><circle cx="12" cy="3" r="2" fill="none" stroke="#333"/></svg>
      <h3>STRATEGY</h3><ul><li>Effective Strategy Meeting</li><li>Strategic Themes 2018 - 2020: Stablize, Accelerate, Surge</li><li>Business Drivers: Drive Revenue, Improve Kestrelite Experience, Increase Brand Awareness</li></ul></div>
    <div class="block"><svg class="icon" viewBox="0 0 15 15"><path d="M2 6 7 1h6v6l-5 5z" fill="none" stroke="#333"/><circle cx="10.5" cy="3.5" r="1" fill="#333"/></svg>
      <h3>SALES</h3><ul><li>Brindlewood Account Transition</li><li>Vantor Account Transition</li><li>2 year Managed Services Engagement Model</li></ul></div>
    <div class="block"><svg class="icon" viewBox="0 0 15 15"><path d="M5 2h5l-1 3c3 1 4 4 4 6 0 2-2 3-5.5 3S2 13 2 11c0-2 1-5 4-6z" fill="none" stroke="#333"/></svg>
      <h3>REVENUE / EBITA</h3><ul><li>$3.8M / 1.44%</li></ul></div>
  </div>
</section>

<section class="season fall">
  <div class="band">FALL</div><div class="tab">Q4 2018</div>
  <div class="notes">
    <div class="block"><svg class="icon" viewBox="0 0 15 15"><circle cx="3" cy="7.5" r="2" fill="none" stroke="#333"/><rect x="10" y="1" width="4" height="4" fill="none" stroke="#333"/><rect x="10" y="10" width="4" height="4" fill="none" stroke="#333"/><path d="M5 7.5h3V3h2M8 7.5V12h2" fill="none" stroke="#333"/></svg>
      <h3>BIZ ARCHITECTURE</h3><ul><li>XF Framework - Functional Meetings &amp;</li><li>Scrum of Scrums</li><li>Structured Reorg</li><li>Implemented Reorg</li><li>Quarterly Org Iteration cadence</li><li>Defined Key Hire Plan</li><li>CR Office Operational</li><li>Time Accountability</li><li>Tools ReConfig</li><li>Org Structure v1</li></ul></div>
    <div class="block"><svg class="icon" viewBox="0 0 15 15"><path d="M1 3l3 3M4 3 1 6M1 10h3M10 12l3-3" fill="none" stroke="#333"/><circle cx="12" cy="3" r="2" fill="none" stroke="#333"/></svg>
      <h3>STRATEGY</h3><ul><li>Internal QBR Accountability</li></ul></div>
    <div class="block"><svg class="icon" viewBox="0 0 15 15"><path d="M2 6 7 1h6v6l-5 5z" fill="none" stroke="#333"/><circle cx="10.5" cy="3.5" r="1" fill="#333"/></svg>
      <h3>SALES</h3><ul><li>Larkspur QBR</li><li>Brindlewood QBR</li></ul></div>
    <div class="block"><svg class="icon" viewBox="0 0 15 15"><path d="M5 2h5l-1 3c3 1 4 4 4 6 0 2-2 3-5.5 3S2 13 2 11c0-2 1-5 4-6z" fill="none" stroke="#333"/></svg>
      <h3>REVENUE / EBITA</h3><ul><li>$4.4M / 0.58%</li></ul></div>
  </div>
</section>

<section class="season winter">
  <div class="band">WINTER</div><div class="tab">Q1 2019</div>
  <div class="notes">
    <div class="block"><svg class="icon" viewBox="0 0 15 15"><circle cx="3" cy="7.5" r="2" fill="none" stroke="#333"/><rect x="10" y="1" width="4" height="4" fill="none" stroke="#333"/><rect x="10" y="10" width="4" height="4" fill="none" stroke="#333"/><path d="M5 7.5h3V3h2M8 7.5V12h2" fill="none" stroke="#333"/></svg>
      <h3>BIZ ARCHITECTURE</h3><ul><li>XF Framework - Progress Demos</li><li>Org Structure - COE's</li><li>Stablize Accounting &amp; Finance</li><li>Exec Hiring Process</li></ul></div>
    <div class="block"><svg class="icon" viewBox="0 0 15 15"><circle cx="6" cy="6" r="5" fill="none" stroke="#333"/><path d="M10 10l4 4" stroke="#333"/></svg>
      <h3>KEY HIRES</h3><ul><li class="plain">Controller</li><li>Director CX</li></ul></div>
    <div class="block"><svg class="icon" viewBox="0 0 15 15"><path d="M1 3l3 3M4 3 1 6M1 10h3M10 12l3-3" fill="none" stroke="#333"/><circle cx="12" cy="3" r="2" fill="none" stroke="#333"/></svg>
      <h3>STRATEGY</h3><ul><li>Founders removed from front line activity</li><li>Kestrel QBR - Goal Setting &amp; Tracking</li></ul></div>
    <div class="block"><svg class="icon" viewBox="0 0 15 15"><path d="M2 6 7 1h6v6l-5 5z" fill="none" stroke="#333"/><circle cx="10.5" cy="3.5" r="1" fill="#333"/></svg>
      <h3>SALES</h3><ul><li class="plain">Vantor QBR</li><li class="plain">Brindlewood QBR</li></ul></div>
    <div class="block"><svg class="icon" viewBox="0 0 15 15"><path d="M5 2h5l-1 3c3 1 4 4 4 6 0 2-2 3-5.5 3S2 13 2 11c0-2 1-5 4-6z" fill="none" stroke="#333"/></svg>
      <h3>REVENUE / EBITA</h3><ul><li class="plain">$4.8M / 12.84%</li></ul></div>
  </div>
</section>

<section class="season spring">
  <div class="band">SPRING</div><div class="tab">Q2 2019</div>
  <div class="notes">
    <div class="block"><svg class="icon" viewBox="0 0 15 15"><circle cx="3" cy="7.5" r="2" fill="none" stroke="#333"/><rect x="10" y="1" width="4" height="4" fill="none" stroke="#333"/><rect x="10" y="10" width="4" height="4" fill="none" stroke="#333"/><path d="M5 7.5h3V3h2M8 7.5V12h2" fill="none" stroke="#333"/></svg>
      <h3>BIZ ARCHITECTURE</h3><ul><li>XF Framework - Ideation Board</li><li>Consulting Levels &amp; Salary Bands</li><li>Roles &amp; Responsibilities</li></ul></div>
    <div class="block"><svg class="icon" viewBox="0 0 15 15"><circle cx="6" cy="6" r="5" fill="none" stroke="#333"/><path d="M10 10l4 4" stroke="#333"/></svg>
      <h3>KEY HIRES</h3><ul><li>Interim HR</li><li class="plain">Provisional Client Partner</li><li>Acting Director 1</li><li>Acting Director 2</li><li>Client Partner 1</li><li>Sales Exec 1</li></ul></div>
    <div class="block"><svg class="icon" viewBox="0 0 15 15"><path d="M2 6 7 1h6v6l-5 5z" fill="none" stroke="#333"/><circle cx="10.5" cy="3.5" r="1" fill="#333"/></svg>
      <h3>SALES</h3><ul><li>Tiered Pricing Managed Services</li><li>Opened Glasshouse Door</li><li>Flipped focus from operationaly run company to sales/marketing driven org</li><li>Pellham Direct</li></ul></div>
    <div class="block"><svg class="icon" viewBox="0 0 15 15"><path d="M5 2h5l-1 3c3 1 4 4 4 6 0 2-2 3-5.5 3S2 13 2 11c0-2 1-5 4-6z" fill="none" stroke="#333"/></svg>
      <h3>REVENUE / EBITA</h3><ul><li>$4.7M / 8.24%</li></ul></div>
  </div>
</section>

<section class="season greenfield">
  <div class="band">GREENFIELD</div><div class="tab">2020</div>
  <div class="notes">
    <div class="block"><h3>GREENFIELD</h3><ul><li>Set 2020 Goals</li><li>Schedule QBRs 1 year out</li><li>Financial Projections</li><li>Fully Functional Leadership Team</li><li>Robust Sales Team</li></ul></div>
    <div class="block"><svg class="icon" viewBox="0 0 15 15"><path d="M5 2h5l-1 3c3 1 4 4 4 6 0 2-2 3-5.5 3S2 13 2 11c0-2 1-5 4-6z" fill="none" stroke="#333"/></svg>
      <h3>REVENUE / EBITA</h3><ul><li>$35M / 15%</li></ul></div>
  </div>
</section>

<div class="value" style="left:148px;top:544px;background:#f4c21c;box-shadow:0 0 0 4px #fbe48a">$3.8M<br>1.44%</div>
<div class="value" style="left:363px;top:572px;background:#3f4b53;box-shadow:0 0 0 4px #6b777e">$4.4M<br>0.58%</div>
<div class="value" style="left:578px;top:526px;background:#a9d8e3;box-shadow:0 0 0 4px #d3eef3">$4.8M<br>12.84%</div>
<div class="value" style="left:826px;top:402px;background:#b3d63e;box-shadow:0 0 0 4px #dcee9a">$4.7M<br>8.24%</div>
<div class="value" style="left:1030px;top:226px;background:#2e8b3a;box-shadow:0 0 0 4px #5aa84a">$35M<br>15%</div>

<div class="label" style="left:58px">STORMING</div>
<div class="label" style="left:275px;color:#fff">ACTIVITY</div>
<div class="label" style="left:492px">MARLOWBEND</div>
<div class="label" style="left:709px">OUTCOMES</div>
<div class="label" style="left:926px;color:#fff">VALUE CREATION</div>
</body>
</html>
```